RWT Fittings Ltd Business Cards

We need a business card with our business logo. We provide window and door installations on high-rises in west coast British Colombia, Canada.

I would like my business information and details on one side of the card, and the other side the company name with logo

Target Market(s)

General Contractors

Industry/Entity Type

Construction

Contact Information for Business Card

one side i want my company name and logo in the dark theme logo that i provided

Requirements
Must have
• Marco Peltieri, 16045518293, RWTFittings@mailbox-demo.com, 1407-5194 Linden Row Burnaby BC, V5H 2K9, Owner & Manager

```html
<!DOCTYPE html>
<html lang="en">
<head>
<meta charset="utf-8">
<title>RWT Fittings Ltd – Business Cards</title>
<link rel="stylesheet" href="https://fonts.googleapis.com/css2?family=Roboto:wght@400;500;700;900&display=swap">
<style>
  :root {
    --stage: #232323;
    --card: #1f2024;
    --card-deep: #1a1b1e;
    --accent: #29abe2;
    --grey: #9a9a9a;
    --ink-light: #f2f2f2;
    --motif: #2a2d33;
    --motif-soft: #26292e;
  }
  * { margin: 0; padding: 0; box-sizing: border-box; }
  html, body {
    width: 1200px; height: 780px; overflow: hidden;
    background: var(--stage);
    font-family: "Roboto", sans-serif;
  }
  .canvas { position: relative; width: 1200px; height: 780px; }

  .card {
    position: absolute;
    width: 560px; height: 320px;
    background: var(--card);
    border-radius: 22px;
    border-bottom: 4px solid var(--accent);
    border-left: 3px solid var(--accent);
    overflow: hidden;
    box-shadow: 0 18px 40px rgba(0,0,0,.55);
  }
  .card--back { left: 60px; top: 60px; }
  .card--front { left: 580px; top: 400px; }

  /* back side */
  .back-pattern {
    position: absolute; inset: 0;
    background: linear-gradient(150deg, #3b3d42 0%, #2a2c31 35%, var(--card-deep) 70%);
  }
  .back-wordmark {
    position: absolute; right: 36px; bottom: 40px;
    display: flex; align-items: center; gap: 8px;
    color: var(--accent); font-weight: 500; font-size: 17px; letter-spacing: .5px;
  }
  .mark-square { width: 12px; height: 12px; background: var(--accent); }

  /* front side */
  .front-decoration {
    position: absolute; right: 0; top: 0; width: 300px; height: 320px;
    background: linear-gradient(160deg, var(--motif) 0%, var(--motif-soft) 55%, var(--card) 100%);
  }
  .front-wordmark {
    position: absolute; left: 30px; top: 34px;
    display: flex; align-items: center; gap: 12px;
    color: var(--accent); font-weight: 700; font-size: 30px; letter-spacing: 1px;
  }
  .front-wordmark .mark-square { width: 26px; height: 26px; }

  .identity {
    position: absolute; right: 48px; top: 86px; text-align: right;
  }
  .identity__name { font-weight: 900; font-size: 27px; line-height: 1; }
  .identity__first { color: var(--accent); }
  .identity__last { color: var(--grey); }
  .identity__role { color: var(--ink-light); font-weight: 500; font-size: 14px; margin-top: 4px; }
  .identity-bar {
    position: absolute; right: 26px; top: 80px; width: 12px; height: 52px; background: var(--accent);
  }

  .contact {
    position: absolute; left: 70px; bottom: 34px;
    color: var(--ink-light); font-size: 14px; line-height: 1.35;
  }
  .contact__address { margin-bottom: 12px; }
  .contact__row { display: flex; align-items: center; gap: 10px; }
  .contact__icon { width: 15px; height: 15px; flex: none; }
</style>
</head>
<body>
<main class="canvas">

  <section class="card card--back" aria-label="Business card back">
    <div class="back-pattern" role="img" aria-label="Repeating company symbol pattern in dark grey tones"></div>
    <div class="back-wordmark"><span class="mark-square"></span>RWT Fittings Ltd</div>
  </section>

  <section class="card card--front" aria-label="Business card front">
    <div class="front-decoration" role="img" aria-label="Large faint company symbol decoration"></div>

    <div class="front-wordmark"><span class="mark-square"></span>RWT FITTINGS LTD</div>

    <div class="identity-bar"></div>
    <div class="identity">
      <p class="identity__name"><span class="identity__first">Marco</span> <span class="identity__last">Peltieri</span></p>
      <p class="identity__role">Owner &amp; Manager</p>
    </div>

    <div class="contact">
      <p class="contact__address">1407-5194 Linden Row<br>Burnaby BC, V5H 2K9</p>
      <p class="contact__row">
        <svg class="contact__icon" viewBox="0 0 24 24" aria-hidden="true"><path fill="#29abe2" d="M6.6 10.8a15.1 15.1 0 0 0 6.6 6.6l2.2-2.2a1 1 0 0 1 1-.25 11.4 11.4 0 0 0 3.6.57 1 1 0 0 1 1 1V20a1 1 0 0 1-1 1A17 17 0 0 1 3 4a1 1 0 0 1 1-1h3.5a1 1 0 0 1 1 1c0 1.25.2 2.45.57 3.57a1 1 0 0 1-.25 1z"/></svg>
        1604 551 8293
      </p>
      <p class="contact__row">
        <svg class="contact__icon" viewBox="0 0 24 24" aria-hidden="true"><rect x="2" y="5" width="20" height="14" rx="2" fill="#29abe2"/><path d="M3 6l9 7 9-7" fill="none" stroke="#1f2024" stroke-width="2"/></svg>
        RWTFittings@mailbox-demo.com
      </p>
    </div>
  </section>

</main>
</body>
</html>
```